QRV Advisors needs a web site

We need a web site for www.qrvadvisors-example.com. QRV is a mergers and acquisition consulting company that focuses our buyer and seller services on logistics companies. We help put companies together, and help with legal and financial due diligence. We want the web site to express our service and show the logistics components. We want personalized images versus pictures of trucks and airplanes.

Our new logo uses Burgandy and grey colors. Image attached. We are not in to bold, big letters...classy, artistic, low key preferred. Confidentiality, experience, professional are what we want to express on the site.

All we expect for the first part of this project is a home page, and one subpage.  We are budgeting other funds for the technical aspects of the web site

Reason: All that I'm seeing so far is trucks, forklifts and planes. We are a legal mergers and acquisitions firm that focus on logistics. I like some of the images to say logistics, but really want it say legal, financial, and putting companies together. Will pay extra for the sub page if someone can impress us with a home page.

Reason: Swamped with another project at the moment...will work on this over the weekend and provide designer feedback and select final design by Tuesday

```html
<!DOCTYPE html>
<html lang="en">
<head>
<meta charset="utf-8">
<title>QRV Advisors – Contact Us</title>
<link rel="stylesheet" href="https://fonts.googleapis.com/css2?family=Cinzel:wght@400;700&family=Lato:wght@400;700&family=Pathway+Gothic+One&display=swap">
<style>
:root{
  --burgundy:#a5123a;
  --burgundy-dark:#7d0b2a;
  --grey-text:#3b3b3b;
  --rule:#cfcfcf;
  --field-border:#c9c9c9;
  --footer-dark:#262626;
  --footer-text:#e8e8e8;
}
*{box-sizing:border-box;margin:0;padding:0}
html,body{width:915px;height:1200px;overflow:hidden}
body{position:relative;background:#fff;font-family:'Lato',sans-serif;color:var(--grey-text)}
.abs{position:absolute}

/* header */
.site-header{left:0;top:0;width:915px;height:87px;background:linear-gradient(#fff,#f1f1f1)}
.brand{left:103px;top:26px;font-weight:700;font-size:27px;color:#4a4a4a;letter-spacing:1px}
.header-phone{left:726px;top:13px;font-size:12px;color:#444;display:flex;align-items:center;gap:5px}
.main-nav{left:372px;top:60px;display:flex;align-items:center;font-size:12px;color:#333}
.main-nav a{color:inherit;text-decoration:none;padding:2px 6px}
.main-nav .sep{width:1px;height:16px;background:#d2d2d2;margin:0 8px}
.main-nav a.active{background:var(--burgundy);color:#fff;font-weight:700;border-radius:2px}

/* banner */
.banner-bg{left:0;top:87px;width:915px;height:228px;background:linear-gradient(90deg,#8ca7c4 0%,#c9d1d8 14%,#9b9b9b 50%,#6b6f73 80%,#c0643a 100%)}
.banner-frame{left:100px;top:107px;width:715px;height:186px;background:#fff;padding:4px}
.banner-photo{width:100%;height:100%;position:relative;background:linear-gradient(90deg,#c8955a 0%,#e3e3e1 25%,#d6d5d2 55%,#b9ab80 100%)}
.banner-title{position:absolute;right:18px;top:55px;font-family:'Cinzel',serif;font-weight:400;font-size:34px;color:#f4eedc;letter-spacing:1px}
.banner-strip{position:absolute;left:0;bottom:0;width:100%;height:33px;background:rgba(30,30,30,.88);color:#fff;font-family:'Cinzel',serif;font-size:15.5px;text-align:center;line-height:33px;letter-spacing:.6px}

/* content */
.content-bg{left:0;top:315px;width:915px;height:620px;background:linear-gradient(#efefef 0,#fff 60px)}
.section-title{font-family:'Cinzel',serif;font-weight:400;font-size:24px;color:#333;width:487px;border-bottom:1px solid var(--rule);padding-bottom:2px;padding-left:2px}
.lede{left:101px;top:380px;font-size:10.5px;color:var(--burgundy)}
.field{border:1px solid var(--field-border);background:#fff;font-size:10px;color:#444;padding:7px 8px;border-radius:2px}
.submit{left:100px;top:615px;width:63px;height:26px;background:var(--burgundy);color:#fff;font-weight:700;font-size:11.5px;text-align:center;line-height:26px;border-radius:2px;letter-spacing:.3px}
.map-area{left:100px;top:705px;width:486px;height:257px;background:linear-gradient(90deg,#e8e3d6 0%,#eae6da 65%,#a9c6ec 78%,#a9c6ec 100%)}

/* sidebar */
.contact-card{left:615px;top:345px;width:200px;height:403px;background:#fff;border:1px solid #d8d8d8;padding:22px 14px 0 15px;box-shadow:inset 0 0 0 4px #f6f6f6}
.contact-card h2{font-size:14.5px;font-weight:700;color:#333;margin-bottom:12px}
.card-lead{font-size:11.5px;line-height:17px;color:#444;margin-bottom:10px}
.card-body{font-size:9.6px;line-height:15.2px;color:#444;margin-bottom:13px}
.card-info{font-size:9.6px;line-height:15.2px;color:#444;margin-bottom:14px}
.card-info b{color:var(--burgundy)}
.card-info u{color:#333}

/* footer */
.footer-wave{left:0;top:935px;width:915px;height:120px;background:linear-gradient(180deg,#fff 0%,#f0e6e9 35%,var(--burgundy-dark) 70%,#8a8a8a 85%,var(--footer-dark) 100%)}
.footer-base{left:0;top:1055px;width:915px;height:145px;background:var(--footer-dark)}
.footer-links{font-size:10px;color:var(--footer-text);line-height:21.5px;list-style:none}
.footer-links li::before{content:"·";margin-right:5px;color:#aaa}
.footer-map{left:365px;top:1089px;width:182px;height:67px;border:2px solid #9e9e9e;background:linear-gradient(90deg,#e6e0cf 0%,#e9e4d6 70%,#a9c6ec 85%)}
.footer-address{left:383px;top:1163px;font-size:9.8px;line-height:13px;color:var(--footer-text)}
.cta{font-family:'Pathway Gothic One',sans-serif;color:#fff;font-size:15px}
.appointment{left:730px;top:1066px;width:73px;height:21px;background:linear-gradient(#fff,#dcdcdc);color:#222;font-family:'Pathway Gothic One',sans-serif;font-size:14px;text-align:center;line-height:21px;border-radius:2px}
.social{left:648px;top:1132px;display:flex;gap:10px}
.social span{width:18px;height:18px;border-radius:50%;background:#c9c9c9}
.copyright{left:620px;top:1177px;font-size:8.8px;color:#ddd}
</style>
</head>
<body>

<header class="abs site-header"></header>
<div class="abs brand">QRV Advisors</div>
<div class="abs header-phone">
  <svg width="11" height="12" viewBox="0 0 24 24" aria-hidden="true"><path fill="#b3133a" d="M6.6 10.8c1.4 2.8 3.8 5.1 6.6 6.6l2.2-2.2c.3-.3.7-.4 1-.2 1.1.4 2.3.6 3.6.6.6 0 1 .4 1 1V20c0 .6-.4 1-1 1C10.6 21 3 13.4 3 4c0-.6.4-1 1-1h3.5c.6 0 1 .4 1 1 0 1.3.2 2.5.6 3.6.1.3 0 .7-.2 1z"/></svg>
  555 010 2468
</div>
<nav class="abs main-nav">
  <a href="#">Home</a><span class="sep"></span>
  <a href="#" class="active">About</a><span class="sep"></span>
  <a href="#">Consulting Services</a><span class="sep"></span>
  <a href="#">News &amp; Events</a><span class="sep"></span>
  <a href="#">FAQ's</a><span class="sep"></span>
  <a href="#">Contact</a>
</nav>

<div class="abs banner-bg" role="img" aria-label="Wide photo of logistics scene with trucks and a dock worker"></div>
<div class="abs banner-frame">
  <div class="banner-photo" role="img" aria-label="Office desk telephone in soft light">
    <div class="banner-title">Contact us</div>
    <div class="banner-strip">We are a legal mergers and acquisitions firm that focus on logistics.</div>
  </div>
</div>

<div class="abs content-bg"></div>

<h1 class="abs section-title" style="left:100px;top:340px">Contact us</h1>
<p class="abs lede">Lorem ipsum dolor sit amet, consectetuer adipiscing elit, sed diam nonummy</p>

<div class="abs field" style="left:100px;top:415px;width:247px;height:26px">Name :</div>
<div class="abs field" style="left:100px;top:447px;width:247px;height:26px">E-mail :</div>
<div class="abs field" style="left:100px;top:479px;width:247px;height:26px">Phone :</div>
<div class="abs field" style="left:100px;top:511px;width:487px;height:97px">Message :</div>
<div class="abs submit">SUBMIT</div>

<h2 class="abs section-title" style="left:100px;top:664px">How To Find Us?</h2>
<div class="abs map-area" role="img" aria-label="Street map of Chicago area with office location markers"></div>

<aside class="abs contact-card">
  <h2>Contact Info</h2>
  <p class="card-lead">Sed ut perspiciatis unde omnislist natus error sit voluptatemo ntim, totam rem aperiam.</p>
  <p class="card-body">Sed ut perspiciatis unde omnis is natu error sit voluptatem accusk doloremo que la udantium, totam rem aperiamn, eaquel ipsa quae ab illo inventore veri tatis etvl quasi architeco beatae vitaev dicta dollar explicabo.</p>
  <p class="card-info"><b>Quorum Route Ventures</b><br><b>U.S.A Offices :</b> Sanfransisco, Miami, Chicago.</p>
  <p class="card-info"><b>Mailing Address :</b> Harbor Point Centre, 2400 North Bay Road -Ste. 200, Boca Vista, FL 33499</p>
  <p class="card-info"><b>Telephone:</b> 555-010-7731<br><b>Fax:</b> 555-010-7732<br><b>E-mail:</b> <u>info@qrvadvisors-example.com</u></p>
</aside>

<div class="abs footer-wave" role="img" aria-label="Decorative burgundy and grey wave band above the footer"></div>
<div class="abs footer-base"></div>

<ul class="abs footer-links" style="left:108px;top:1114px"><li>Home</li><li>About</li><li>Consulting Services</li></ul>
<ul class="abs footer-links" style="left:222px;top:1114px"><li>News &amp; Events</li><li>FAQ's</li><li>Contact</li></ul>

<div class="abs footer-map" role="img" aria-label="Small map of downtown Chicago office locations"></div>
<svg class="abs" style="left:364px;top:1165px" width="14" height="20" viewBox="0 0 14 20" aria-hidden="true"><path fill="#fff" d="M7 0C3.1 0 0 3.1 0 7c0 5 7 13 7 13s7-8 7-13c0-3.9-3.1-7-7-7zm0 9.5A2.5 2.5 0 1 1 7 4.5a2.5 2.5 0 0 1 0 5z"/></svg>
<div class="abs footer-address">Quorum Route Ventures<br>Sanfransisco, Miami, Chicago.</div>

<div class="abs cta" style="left:593px;top:1067px">Schedule Free Consultation</div>
<div class="abs appointment">Appointment</div>
<div class="abs cta" style="left:594px;top:1090px">Or Call Us on : (555) 010 2468</div>
<div class="abs social"><span></span><span></span><span></span><span></span></div>
<div class="abs copyright">© Copyright 2013 Quorum Route Ventures.</div>

</body>
</html>
```